Meridale Partners Website

Meridale Partners (MP) provide Analytics & Enterprise Performance Management (EPM) advisory & consultancy services. We are passionate about data and making a difference for our clients by working in partnership with them, helping them on their journey to becoming an Meridale Partner. We deliver insights which give our clients a competitive edge and a much deeper understanding of their organisation.

We need a website which shows who we are, what we do and how we do it.

www.meridale-partners.example is our very basic website at the moment. We want to completely revamp it with a corporate look

```html
<!DOCTYPE html>
<html lang="en">
<head>
<meta charset="utf-8">
<title>Meridale Partners — Data Analytics &amp; EPM Consulting</title>
<link rel="stylesheet" href="https://fonts.googleapis.com/css2?family=Poppins:wght@300;400;500;600;700;800&display=swap">
<style>
:root{
  --brand:#2b5874;
  --brand-deep:#234d67;
  --band:#2e6282;
  --band-dark:#1f4a64;
  --footer:#1d4560;
  --ink:#3d3d3d;
  --white:#ffffff;
  --black:#050505;
  --line:#5d86a0;
}
*{box-sizing:border-box;margin:0;padding:0}
html,body{width:1200px;height:4047px;overflow:hidden}
body{position:relative;font-family:"Poppins",sans-serif;color:var(--ink);background:var(--white)}
.abs{position:absolute}

/* header */
.site-header{left:0;top:0;width:1200px;height:70px;background:var(--white);box-shadow:0 1px 4px rgba(0,0,0,.08);z-index:5}
.brand{left:112px;top:10px;display:flex;align-items:center;gap:12px}
.brand-dot{width:46px;height:46px;border-radius:50%;border:6px solid var(--brand)}
.brand-name{font-weight:600;font-size:18px;line-height:20px;color:var(--brand);letter-spacing:.5px;text-transform:uppercase}
.nav{left:606px;top:0;height:70px;display:flex;align-items:center;gap:33px;font-size:13.5px;color:#333}
.nav .active{color:var(--brand)}
.nav .phone{display:flex;align-items:center;gap:8px}

/* hero */
.hero{left:0;top:70px;width:1200px;height:650px;overflow:hidden}
.hero-photo{width:100%;height:100%;
  background:
    radial-gradient(ellipse 260px 300px at 620px 260px,rgba(70,60,52,.55),transparent 70%),
    radial-gradient(ellipse 220px 260px at 900px 220px,rgba(120,90,70,.5),transparent 70%),
    radial-gradient(ellipse 300px 220px at 160px 120px,rgba(92,110,70,.55),transparent 70%),
    radial-gradient(ellipse 260px 160px at 700px 560px,rgba(40,44,48,.5),transparent 70%),
    linear-gradient(110deg,#c7b79c 0%,#a99a80 25%,#d8d2c6 50%,#bfb8ae 70%,#8d8a86 100%)}
.hero-wave{left:0;bottom:0}
.hero-badge{left:58px;top:138px;width:370px;height:370px;border-radius:50%;background:rgba(43,96,126,.85);color:var(--white);text-align:center;padding-top:128px}
.hero-badge h1{font-weight:700;font-size:29px;line-height:40px}
.hero-badge p{font-size:16.5px;line-height:38px;text-transform:uppercase;letter-spacing:.2px;margin-top:2px}
.slider-dots{left:563px;top:576px;display:flex;gap:4px}
.slider-dots span{width:10px;height:10px;border-radius:50%;border:1.5px solid var(--white)}
.slider-dots span:first-child{background:var(--white)}

/* who we are */
.who-photo{left:112px;top:795px;width:433px;height:450px;border-radius:55px;
  background:
    radial-gradient(ellipse 140px 90px at 230px 250px,rgba(60,50,48,.45),transparent 70%),
    radial-gradient(ellipse 90px 120px at 360px 230px,rgba(70,110,60,.45),transparent 70%),
    linear-gradient(180deg,#eef0ee 0%,#d3d6d3 40%,#9a9c97 75%,#5f615d 100%);
  box-shadow:0 8px 22px rgba(0,0,0,.18)}
.who-copy{left:600px;top:880px;width:480px}
.section-title{font-weight:700;font-size:40px;color:var(--brand);line-height:52px}
.rule{width:94px;height:3px;background:var(--brand);margin-top:10px}
.body-text{font-size:13.5px;line-height:27.5px;color:#555}
.who-copy .body-text{margin-top:30px}
.who-copy .call{margin-top:15px}
.call a{color:var(--brand);text-decoration:none}

/* what we do */
.services-band{left:0;top:1318px;width:1200px;height:554px;
  background:
    radial-gradient(ellipse 120px 260px at 400px 1560px,rgba(20,50,70,.35),transparent 70%),
    radial-gradient(ellipse 320px 200px at 950px 150px,rgba(120,160,190,.18),transparent 70%),
    linear-gradient(180deg,var(--band) 0%,var(--band-dark) 100%)}
.services-title{left:0;top:1366px;width:1200px;text-align:center;color:var(--white);font-weight:700;font-size:40px}
.service{top:1493px;width:318px;height:311px;text-align:center;color:var(--white)}
.service.featured{border:1.5px solid rgba(255,255,255,.85)}
.service-icon{display:block;margin:28px auto 0}
.service h3{font-weight:600;font-size:16px;margin-top:18px}
.service p{font-size:12px;line-height:24px;margin:12px auto 0;width:300px}
.service .go{margin-top:18px}

/* how we do it */
.how-title{left:0;top:1952px;width:1200px;text-align:center}
.how-title .rule{margin:8px auto 0}
.how-photo{width:458px;height:381px;box-shadow:0 6px 18px rgba(0,0,0,.15)}
.photo-a{left:112px;top:2082px;background:
    radial-gradient(ellipse 120px 150px at 90px 130px,rgba(80,60,48,.5),transparent 70%),
    radial-gradient(ellipse 130px 150px at 360px 140px,rgba(40,50,66,.5),transparent 70%),
    radial-gradient(ellipse 220px 110px at 240px 320px,rgba(140,100,70,.55),transparent 70%),
    linear-gradient(135deg,#e4ddd2,#bfb4a6 50%,#a58e78)}
.photo-b{left:628px;top:2523px;background:
    radial-gradient(ellipse 140px 190px at 270px 250px,rgba(30,42,62,.7),transparent 70%),
    radial-gradient(ellipse 110px 170px at 420px 200px,rgba(30,40,58,.6),transparent 70%),
    radial-gradient(ellipse 110px 90px at 250px 120px,rgba(200,170,150,.5),transparent 70%),
    linear-gradient(120deg,#f4f2ee 0%,#e3e0da 35%,#8e96a3 70%,#404b5d 100%)}
.photo-c{left:112px;top:2966px;background:
    radial-gradient(ellipse 150px 200px at 200px 250px,rgba(70,95,100,.6),transparent 70%),
    radial-gradient(ellipse 110px 180px at 370px 200px,rgba(50,40,36,.5),transparent 70%),
    radial-gradient(ellipse 90px 120px at 60px 150px,rgba(60,64,68,.5),transparent 70%),
    linear-gradient(135deg,#dfe4e6,#aab6ba 50%,#6e7e84)}
.how-copy{width:480px}
.how-copy h2{font-weight:600;font-size:24px;color:#2a2a2a;line-height:32px}
.how-copy .body-text{font-size:12.8px;line-height:26px;margin-top:14px;color:#666}
.copy-a{left:602px;top:2166px}
.copy-b{left:112px;top:2608px;width:485px}
.copy-c{left:602px;top:3050px}
.connector{left:0;top:0}

/* contact */
.contact-band{left:0;top:3432px;width:1200px;height:563px;background:linear-gradient(180deg,var(--band) 0%,var(--brand-deep) 100%)}
.contact-box{left:112px;top:3493px;width:976px;height:322px;border:3px solid var(--white);text-align:center;color:var(--white)}
.contact-box h2{font-weight:700;font-size:44px;line-height:56px;margin-top:42px}
.contact-box .tagline{font-weight:500;font-size:15px;margin-top:14px}
.actions{display:flex;justify-content:center;gap:16px;margin-top:24px}
.btn{width:208px;height:50px;border-radius:25px;display:flex;align-items:center;justify-content:center;gap:8px;font-size:15px;font-weight:500;color:var(--white)}
.btn-outline{border:1.5px solid rgba(255,255,255,.85)}
.btn-solid{background:var(--black)}
.contact-info{left:0;width:1200px;text-align:center;color:var(--white);font-size:15px;display:flex;justify-content:center;align-items:center;gap:8px}
.partner-badge{left:520px;top:3942px;width:160px;height:26px;border-radius:3px;background:rgba(255,255,255,.3)}

/* footer */
.site-footer{left:0;top:3995px;width:1200px;height:52px;background:var(--footer);color:var(--white);font-size:12.5px}
.social{left:112px;top:19px;display:flex;gap:10px}
.social span{width:14px;height:14px;border-radius:50%;background:var(--white)}
.copyright{left:0;top:17px;width:1200px;text-align:center}
.policy{left:995px;top:15px;font-size:14px}
</style>
</head>
<body>

<header class="abs site-header">
  <div class="abs brand">
    <span class="brand-dot"></span>
    <span class="brand-name">Meridale<br>Partners</span>
  </div>
  <nav class="abs nav">
    <span class="active">Home</span>
    <span>Services</span>
    <span>About Us</span>
    <span>Contact Us</span>
    <span class="phone">
      <svg width="12" height="12" viewBox="0 0 24 24"><path fill="#2b5874" d="M6.6 10.8a15 15 0 006.6 6.6l2.2-2.2a1 1 0 011-.25 11.4 11.4 0 003.6.57 1 1 0 011 1V20a1 1 0 01-1 1A17 17 0 013 4a1 1 0 011-1h3.5a1 1 0 011 1c0 1.25.2 2.45.57 3.57a1 1 0 01-.25 1z"/></svg>
      +1 01 555 0142
    </span>
  </nav>
</header>

<section class="abs hero">
  <div class="hero-photo" role="img" aria-label="Photo of three colleagues working together around a laptop in a bright office"></div>
  <svg class="abs hero-wave" width="1200" height="80" viewBox="0 0 1200 80"><path fill="#fff" d="M0 62 C300 40 520 18 760 30 C960 40 1100 62 1200 66 L1200 80 L0 80Z"/></svg>
  <div class="abs hero-badge">
    <h1>Meridale Partners</h1>
    <p>Data Analytics &amp; EPM Consulting<br>Services</p>
  </div>
  <div class="abs slider-dots"><span></span><span></span><span></span><span></span><span></span></div>
</section>

<section>
  <div class="abs who-photo" role="img" aria-label="Photo of a team meeting around a table in a modern glass office"></div>
  <div class="abs who-copy">
    <h2 class="section-title">Who We Are</h2>
    <div class="rule"></div>
    <p class="body-text">Meridale Partners is an exciting start-up in the Data Analytics and EPM space.&nbsp; Founded in 2019, MP specialise in the implementation and support of BI, EPM and Data Analytics business solutions, both in the Cloud and on-premise.</p>
    <p class="body-text call"><a>Call us on 01 555 0142</a> or <a>email: info@meridale-partners.example</a> for more information</p>
  </div>
</section>

<section>
  <div class="abs services-band"></div>
  <h2 class="abs services-title">What We Do</h2>

  <div class="abs service" style="left:96px">
    <svg class="service-icon" width="92" height="92" viewBox="0 0 92 92" fill="none" stroke="#fff" stroke-width="2.2" stroke-linejoin="round" stroke-linecap="round" role="img" aria-label="Consulting desk icon">
      <path d="M40 6h30v18H56l-6 6v-6H40z"/>
      <path d="M46 12h18M46 18h12"/>
      <rect x="20" y="44" width="52" height="6"/>
      <path d="M26 50v36M66 50v36M26 66h40"/>
      <rect x="34" y="30" width="24" height="14"/>
      <path d="M8 86h76"/>
    </svg>
    <h3>Advise &amp; Architect Services</h3>
    <p>Helping our customers understand the art of the possible and safeguarding their investments by overseeing implementations.</p>
  </div>

  <div class="abs service featured" style="left:445px">
    <svg class="service-icon" width="92" height="92" viewBox="0 0 92 92" fill="none" stroke="#fff" stroke-width="2.2" stroke-linejoin="round" stroke-linecap="round" role="img" aria-label="Computer screen icon">
      <rect x="8" y="10" width="76" height="54" rx="3"/>
      <path d="M8 54h76M38 64l-4 14h24l-4-14M28 80h36"/>
      <rect x="16" y="18" width="28" height="28"/>
      <path d="M16 40l9-9 7 7 5-5 7 7"/>
      <path d="M52 20h24M52 28h24M52 36h16M52 44h20"/>
    </svg>
    <h3>Design &amp; Implement</h3>
    <p>Working with the project management team, through each stage of the project, with clearly defined deliverables and well exercised</p>
    <svg class="go" width="32" height="14" viewBox="0 0 32 14"><path d="M1 7h29M24 1l6 6-6 6" fill="none" stroke="#fff" stroke-width="1.6"/></svg>
  </div>

  <div class="abs service" style="left:783px">
    <svg class="service-icon" width="92" height="92" viewBox="0 0 92 92" fill="none" stroke="#fff" stroke-width="2.2" stroke-linejoin="round" stroke-linecap="round" role="img" aria-label="Gear and bar chart icon">
      <circle cx="38" cy="52" r="22"/>
      <circle cx="38" cy="52" r="9"/>
      <path d="M38 24v-6M38 86v-6M10 52h6M60 52h6M18 32l4 4M54 68l4 4M18 72l4-4"/>
      <rect x="50" y="48" width="8" height="26"/>
      <rect x="62" y="36" width="8" height="38"/>
      <rect x="74" y="22" width="8" height="52"/>
      <path d="M48 36l14-12 10 6 12-16M78 14h6v6"/>
    </svg>
    <h3>Optimise &amp; Manage</h3>
    <p>Our Managed Services delivers proactive, on-demand support for EPM and Data Analytics environments.</p>
  </div>
</section>

<section>
  <div class="abs how-title">
    <h2 class="section-title">How We Do It</h2>
    <div class="rule"></div>
  </div>
  <svg class="abs connector" width="1200" height="4047" viewBox="0 0 1200 4047">
    <path d="M338 2463V2497H861V2523M861 2904V2937H338V2966" fill="none" stroke="#5d86a0" stroke-width="1.5"/>
  </svg>

  <div class="abs how-photo photo-a" role="img" aria-label="Photo of colleagues discussing reports around a meeting table"></div>
  <div class="abs how-copy copy-a">
    <h2>Analytics</h2>
    <p class="body-text">Lorem ipsum dolor sit amet, consectetur adipiscing elit, sed do eiusmod tempor incididunt ut labore et dolore magna aliqua. Ut enim ad minim veniam, quis nostrud exercitation ullamco laboris nisi ut consequat. Duis aute reprehenderit in voluptate velit esse cillum dolore eu fugiat nulla pariatur. Excepteur sint occaecat cupidatat non proident, sunt in culpa qui officia deserunt mollit anim id est laborum</p>
  </div>

  <div class="abs how-photo photo-b" role="img" aria-label="Photo of two businessmen reviewing a tablet"></div>
  <div class="abs how-copy copy-b">
    <h2>Enterprise Performance Management</h2>
    <p class="body-text">Lorem ipsum dolor sit amet, consectetur adipiscing elit, sed do eiusmod tempor incididunt ut labore et dolore magna aliqua. Ut enim ad minim veniam, quis nostrud exercitation ullamco laboris nisi ut consequat. Duis aute reprehenderit in voluptate velit esse cillum dolore eu fugiat nulla pariatur. Excepteur sint occaecat cupidatat non proident, sunt in culpa qui officia deserunt mollit anim id est laborum</p>
  </div>

  <div class="abs how-photo photo-c" role="img" aria-label="Photo of two consultants in conversation at a desk"></div>
  <div class="abs how-copy copy-c">
    <h2>Advisory &amp; Consultancy Services.</h2>
    <p class="body-text">Lorem ipsum dolor sit amet, consectetur adipiscing elit, sed do eiusmod tempor incididunt ut labore et dolore magna aliqua. Ut enim ad minim veniam, quis nostrud exercitation ullamco laboris nisi ut consequat. Duis aute reprehenderit in voluptate velit esse cillum dolore eu fugiat nulla pariatur. Excepteur sint occaecat cupidatat non proident, sunt in culpa qui officia deserunt mollit anim id est laborum</p>
  </div>
</section>

<section>
  <div class="abs contact-band"></div>
  <div class="abs contact-box">
    <h2>Contact Us To Discuss Your<br>Business Needs</h2>
    <p class="tagline">Advise &amp; Architect | Design &amp; Implement | Optimise &amp; Manage</p>
    <div class="actions">
      <span class="btn btn-outline">
        <svg width="13" height="13" viewBox="0 0 24 24"><path fill="#fff" d="M6.6 10.8a15 15 0 006.6 6.6l2.2-2.2a1 1 0 011-.25 11.4 11.4 0 003.6.57 1 1 0 011 1V20a1 1 0 01-1 1A17 17 0 013 4a1 1 0 011-1h3.5a1 1 0 011 1c0 1.25.2 2.45.57 3.57a1 1 0 01-.25 1z"/></svg>
        +1 01 555 0142
      </span>
      <span class="btn btn-solid">Contact Us</span>
    </div>
  </div>
  <p class="abs contact-info" style="top:3872px">
    <svg width="11" height="15" viewBox="0 0 12 16"><path fill="#fff" d="M6 0a6 6 0 00-6 6c0 4.5 6 10 6 10s6-5.5 6-10a6 6 0 00-6-6zm0 8.2A2.2 2.2 0 116 3.8a2.2 2.2 0 010 4.4z"/></svg>
    48 Harbour Row, Eastgate, Dublin 4, D04 KT21
  </p>
  <p class="abs contact-info" style="top:3905px">
    <svg width="14" height="11" viewBox="0 0 16 12"><path fill="#fff" d="M0 0h16v1.5L8 7 0 1.5zM0 3.3l8 5.5 8-5.5V12H0z"/></svg>
    info@meridale-partners.example
  </p>
  <div class="abs partner-badge" role="img" aria-label="Technology partner badge"></div>
</section>

<footer class="abs site-footer">
  <div class="abs social"><span></span><span></span></div>
  <p class="abs copyright">© 2022 All Rights Reserved</p>
  <p class="abs policy">Privacy Policy</p>
</footer>

</body>
</html>
```